Signage Design Project

We need a logo and signage for the shopfront of a personal fitness training gym and coaching facility. We want the signage to cover the glass shopfront windows which consist of 4 glass windows with dimensions: 1 of 200cm x 180cm, 2 of 180cm x 135cm and 1 of 180cm x 180cm. The windows that are 200x 180 and 180x180 are the most visable/ important. We want the 200x180 to display the logo and our name which is "Ridgeline Fitness Centre" with further information of: Your personal training studio and boutique coaching gym Ph: 9471 2836.
For the window with 180 x 180cm measurement we want to list the services we provide which are:
Personal Training Sessions | Group Classes|Weight Loss |Toning & Sculpting|Bodybuilding I Cardio|Weights| Kettlebells| Boxing| Circuits I Team Building Programs| Boot Camp I Healthy Lifestyle & Wellness Coaching
The 2 windows 180x135cm are diagonal to the entry of the shop. We want them to be the same and plainer in design with the words: Ridgeline Fitness Centre
Personal Training Studio and Boutique Coaching Gym
The signage design also includes an acrylic window box that lights up which is to display the logo and Ridgeline Fitness Centre

```html
<!DOCTYPE html>
<html lang="en">
<head>
<meta charset="utf-8">
<title>Ridgeline Fitness Centre – Window Signage Options</title>
<link rel="stylesheet" href="https://fonts.googleapis.com/css2?family=Questrial&family=Ubuntu:wght@500&display=swap">
<style>
  :root {
    --page-bg: #ffffff;
    --sign-deep: #0092b8;
    --sign-mid: #00a6d6;
    --sign-bright: #00b8ec;
    --sign-text: #ffffff;
    --label-teal: #1b9ab9;
  }
  * { margin: 0; padding: 0; box-sizing: border-box; }
  html, body {
    width: 1200px;
    height: 900px;
    overflow: hidden;
    background: var(--page-bg);
  }
  .sheet {
    position: relative;
    width: 1200px;
    height: 900px;
  }
  .sign-option {
    position: absolute;
    top: 237px;
    width: 565px;
    height: 465px;
  }
  .sign-option--a { left: 19px; }
  .sign-option--b { left: 620px; }
  .sign-shape {
    position: absolute;
    inset: 0;
    width: 565px;
    height: 465px;
  }
  .sign-content {
    position: absolute;
    left: 0;
    width: 565px;
    text-align: center;
    color: var(--sign-text);
    font-family: "Questrial", "Century Gothic", sans-serif;
  }
  .brand-name {
    top: 128px;
    font-size: 50px;
    line-height: 1.12;
    font-weight: 400;
    letter-spacing: 2px;
  }
  .tagline {
    top: 274px;
    font-size: 26px;
    line-height: 29px;
    letter-spacing: 2.6px;
  }
  .phone {
    top: 384px;
    font-size: 44px;
    line-height: 1;
    letter-spacing: 3px;
  }
  .option-label {
    position: absolute;
    top: 750px;
    width: 60px;
    text-align: center;
    font-family: "Ubuntu", "Trebuchet MS", sans-serif;
    font-weight: 500;
    font-size: 34px;
    color: var(--label-teal);
  }
  .option-label--a { left: 272px; }
  .option-label--b { left: 872px; }
</style>
</head>
<body>
<main class="sheet">

  <section class="sign-option sign-option--a" aria-label="Signage option A">
    <svg class="sign-shape" viewBox="0 0 565 465" aria-hidden="true">
      <defs>
        <linearGradient id="sign-fill-a" x1="0" y1="1" x2="1" y2="0.3">
          <stop offset="0" stop-color="var(--sign-deep)"/>
          <stop offset="0.55" stop-color="var(--sign-mid)"/>
          <stop offset="1" stop-color="var(--sign-bright)"/>
        </linearGradient>
      </defs>
      <path d="M0 33 C8 68 48 88 110 84 C210 77 300 0 420 0 C500 0 548 48 565 103 V465 H0 Z" fill="url(#sign-fill-a)"/>
    </svg>
    <h1 class="sign-content brand-name">Ridgeline<br>Fitness Centre</h1>
    <p class="sign-content tagline">Your personal training<br>studio &amp; boutique<br>coaching gym</p>
    <p class="sign-content phone">Ph: 9471 2836</p>
  </section>

  <section class="sign-option sign-option--b" aria-label="Signage option B">
    <svg class="sign-shape" viewBox="0 0 565 465" aria-hidden="true">
      <defs>
        <linearGradient id="sign-fill-b" x1="0" y1="1" x2="1" y2="0.3">
          <stop offset="0" stop-color="var(--sign-deep)"/>
          <stop offset="0.55" stop-color="var(--sign-mid)"/>
          <stop offset="1" stop-color="var(--sign-bright)"/>
        </linearGradient>
      </defs>
      <path d="M0 33 C8 68 48 88 110 84 C210 77 300 0 420 0 C500 0 548 48 565 103 V465 H0 Z" fill="url(#sign-fill-b)"/>
    </svg>
    <h2 class="sign-content brand-name">Ridgeline<br>Fitness Centre</h2>
    <p class="sign-content tagline">Your personal training<br>studio &amp; boutique<br>coaching gym</p>
    <p class="sign-content phone">Ph: 9471 2836</p>
  </section>

  <p class="option-label option-label--a">A</p>
  <p class="option-label option-label--b">B</p>

</main>
</body>
</html>
```